Looking for a dynamic business card for a pizzeria.

A business card with our food, logo, and space for name, title, email, website, phone. The card should convey quality, unique, amazing. On the front, I envision food photo or photos with the owners names and contact information. On the back, more food with locations, website, facebook, twitter, instagram icons. It should look polished, not cartoonish, or plain.
Target Market(s)
upscale, local food buyers, 30-50 years in age.
Industry/Entity Type
Restaurant
Contact Information for Business Card
Business Name: Bru'nettix, LLC
Website: www.brunettix.com
Back:
2 locations: (can list on the back of card)
1. Harborview
4087 Corlan Avenue
Marlow, WA 98437
360-481-5067
2. Cedar Ridge
7315 Wendmere Road
Marlow, WA 98431
360-293-8840
front:
EDITABLE space for
Business name
Person's Name
title
2nd title
Email address
cell-phone number
Requirements
Must have
- logo
- my food photo or photos (no watermarks showing)
- locations on back
- Person contact information on front
- full bleed

```html
<!DOCTYPE html>
<html lang="en">
<head>
<meta charset="utf-8">
<title>Bru'nettix Business Cards</title>
<link rel="stylesheet" href="https://fonts.googleapis.com/css2?family=Questrial&display=swap">
<style>
  :root {
    --page: #e9e4dc;
    --card-white: #ffffff;
    --strip-grey: #f1f1f1;
    --brand-green: #2f6b3c;
    --brand-red: #b5161b;
    --red-deep: #8e0f13;
    --ray-pink: #f6dede;
    --text-dark: #2a2a2a;
    --text-light: #ffffff;
    --photo-warm: #c7742e;
    --photo-dark: #5a2a10;
    --photo-light: #f1b65a;
  }
  * { box-sizing: border-box; margin: 0; padding: 0; }
  html, body {
    width: 1200px; height: 843px; overflow: hidden;
    background: var(--page);
    font-family: "Questrial", "Century Gothic", sans-serif;
  }
  .sheet {
    width: 1200px; height: 843px;
    display: flex; align-items: center; justify-content: center; gap: 40px;
  }
  .card {
    position: relative; width: 540px; height: 309px; overflow: hidden;
    background: var(--card-white);
    box-shadow: 0 6px 18px rgba(0,0,0,.18);
  }

  /* Locations side */
  .food-photo {
    position: absolute; left: 0; top: 0; width: 100%; height: 200px;
    background:
      radial-gradient(ellipse at 70% 10%, var(--photo-light) 0%, transparent 55%),
      linear-gradient(180deg, var(--photo-warm) 0%, #a4521f 55%, var(--photo-dark) 100%);
  }
  .wordmark {
    display: flex; align-items: center; gap: 10px;
    color: var(--brand-green); letter-spacing: 1px;
  }
  .wordmark .mark-dot {
    border-radius: 50%; background: var(--brand-red);
  }
  .locations .wordmark {
    position: absolute; left: 22px; top: 26px; font-size: 38px;
  }
  .locations .wordmark .mark-dot { width: 34px; height: 34px; }
  .location-strip {
    position: absolute; left: 0; bottom: 0; width: 100%; height: 109px;
    background: var(--strip-grey);
    display: flex; justify-content: space-between; padding: 14px 22px;
    color: var(--text-dark); font-size: 15px; line-height: 1.25;
  }
  .location .area { color: var(--brand-green); }
  .location .label { color: var(--brand-green); }
  .location.right { text-align: right; }

  /* Contact side */
  .contact .header-zone {
    position: absolute; left: 0; top: 0; width: 100%; height: 142px;
    background: radial-gradient(ellipse at 65% 100%, var(--card-white) 0%, var(--ray-pink) 90%);
  }
  .contact .wordmark {
    position: absolute; left: 0; right: 0; top: 48px;
    justify-content: center; font-size: 44px;
  }
  .contact .wordmark .mark-dot { width: 42px; height: 42px; }
  .rule {
    position: absolute; left: 0; top: 142px; width: 100%; height: 3px;
    background: var(--brand-green);
  }
  .red-band {
    position: absolute; left: 0; top: 145px; width: 100%; height: 164px;
    background: linear-gradient(180deg, var(--brand-red) 0%, var(--red-deep) 100%);
    color: var(--text-light);
  }
  .social {
    position: absolute; left: 26px; top: 16px; display: flex; gap: 8px;
  }
  .social span { width: 16px; height: 16px; border-radius: 50%; background: var(--text-light); }
  .details {
    position: absolute; left: 26px; top: 46px; list-style: none;
    font-size: 15px; line-height: 1.45;
  }
  .details li { display: flex; align-items: center; gap: 9px; }
  .details svg { width: 13px; height: 13px; fill: var(--text-light); }
  .person {
    position: absolute; right: 28px; bottom: 22px; text-align: right;
  }
  .person .name { font-size: 21px; letter-spacing: .5px; }
  .person .title { font-size: 15px; }
</style>
</head>
<body>
<main class="sheet">

  <section class="card locations">
    <div class="food-photo" role="img" aria-label="Photo of pizzas baking in a warm wood-fired oven"></div>
    <div class="wordmark"><span>BRU'NETTIX</span><span class="mark-dot"></span></div>
    <div class="location-strip">
      <div class="location left">
        <div class="area">Cedar Ridge</div>
        <div>7315 Wendmere Road</div>
        <div>Marlow, WA 98431</div>
        <div><span class="label">Phone:</span>360-293-8840</div>
      </div>
      <div class="location right">
        <div class="area">Harborview</div>
        <div>4087 Corlan Avenue</div>
        <div>Marlow, WA 98437</div>
        <div><span class="label">Phone:</span>360-481-5067</div>
      </div>
    </div>
  </section>

  <section class="card contact">
    <div class="header-zone"></div>
    <div class="wordmark"><span>BRU'NETTIX</span><span class="mark-dot"></span></div>
    <div class="rule"></div>
    <div class="red-band">
      <div class="social"><span></span><span></span></div>
      <ul class="details">
        <li>
          <svg viewBox="0 0 12 12"><rect x="3" y="0" width="6" height="12" rx="1"/><rect x="4" y="1.5" width="4" height="7" fill="#b5161b"/></svg>
          689 514 7730
        </li>
        <li>
          <svg viewBox="0 0 12 12"><rect x="0" y="2" width="12" height="8"/><path d="M0 2 L6 7 L12 2" fill="none" stroke="#b5161b" stroke-width="1"/></svg>
          name@brunettix.com
        </li>
        <li>
          <svg viewBox="0 0 12 12"><circle cx="6" cy="6" r="6"/><path d="M0 6 H12 M6 0 V12" stroke="#b5161b" stroke-width="1"/></svg>
          www.brunettix.com
        </li>
      </ul>
      <div class="person">
        <div class="name">DANIEL REYES</div>
        <div class="title">Founder</div>
      </div>
    </div>
  </section>

</main>
</body>
</html>
```